Refresh of far from plain IT company website

Our web site is starting to show it's age. You can see the existing site here: www.plumbwick.net. As a growing company we want to come across as a dynamic collection of IT experts.

We want to update the design so are open to any colour palette and look, but want to retain our current table logo. We use the logo on our business cards but with a white background - see the attached file, so you don't need to keep the brown or the green.

The design should consider the range of browsers that will be looking at the site - so please show how it will look on a wide screen laptop and a 768x1024 tablet.

We want to add some pages about our team and their skills, probably with photos of each person on the team.

This is an uncoded project - the PSD files of the design is required, not coding.
Updates

Thanks everyone for the submissions so far.  It's a holiday day in the UK today but we will get some feedback on the designs so far out to you.

Target Market(s)

Architects and other creative types looking for IT support

Industry/Entity Type

Business

Font styles to use
Serif
Sans Serif

Requirements
Must have
• Must look good on a laptop and an iPad.

```html
<!DOCTYPE html>
<html lang="en">
<head>
<meta charset="utf-8">
<title>plumbwick — Serious IT support for business</title>
<link href="https://fonts.googleapis.com/css2?family=Roboto:wght@300;400;500;700&family=Delius&display=swap" rel="stylesheet">
<style>
:root{
  --plum:#8a1050;
  --gold:#d9a400;
  --mauve:#8e5a8c;
  --mauve-deep:#6f4470;
  --ink:#333;
  --mist:#ebebeb;
  --leaf:#9fd266;
  --leaf-dark:#8cc653;
  --lavender:#b08ee0;
  --night:#0d0d0d;
}
*{margin:0;padding:0;box-sizing:border-box}
html,body{width:690px;height:1200px;overflow:hidden;background:#fff}
body{position:relative;font-family:"Roboto",Arial,sans-serif;color:var(--ink)}
.abs{position:absolute}

/* header */
.topline{left:0;top:0;width:690px;height:3px;background:var(--plum)}
.brand{left:115px;top:14px;display:flex;align-items:center;gap:8px}
.brand-mark{width:18px;height:18px;background:var(--gold)}
.brand-name{font-size:21px;font-weight:700;color:var(--plum);letter-spacing:.2px}
.nav{left:318px;top:22px;display:flex;gap:13px;font-size:6px;color:#222}
.nav a{color:inherit;text-decoration:none;position:relative}
.nav .active{color:var(--plum)}
.nav .active::after{content:"";position:absolute;left:3px;right:3px;top:9px;height:1px;background:var(--plum)}

/* hero */
.hero{left:0;top:50px;width:690px;height:272px;background:linear-gradient(180deg,#454a4c 0%,#33383a 55%,#222628 100%)}
.hero-title{left:294px;top:176px;font-size:18px;font-weight:400;color:#fff}
.hero-arrow{top:170px;width:18px;height:19px;background:#111;display:flex;align-items:center;justify-content:center}
.hero-dots{left:327px;top:303px;display:flex;gap:5px}
.hero-dots span{width:5px;height:5px;border-radius:50%;background:#fff}
.hero-dots .on{background:var(--plum)}

/* welcome */
.welcome{left:0;top:322px;width:690px;height:96px;background:var(--mist)}
.section-title{font-size:15px;font-weight:400;color:var(--plum);text-align:center;width:690px;left:0}
.section-title em{font-style:normal;color:var(--gold)}
.welcome-text{left:117px;top:352px;width:456px;font-size:5.4px;line-height:13.7px;color:#555;text-align:center}

/* services */
.services{left:112px;top:456px;width:466px;display:flex;justify-content:space-between}
.service{width:86px;text-align:center}
.service svg{display:block;margin:0 auto;height:22px}
.service h3{font-size:6.5px;font-weight:400;color:#222;margin-top:10px}
.service p{font-size:4.8px;line-height:8.2px;color:#666;margin-top:4px}
.more{font-size:5.4px;color:var(--plum);display:inline-block;margin-top:3px}

/* what we do */
.app{left:0;top:555px;width:690px;height:179px;background:var(--mauve)}
.app-visual{left:100px;top:565px;width:240px;height:169px;background:linear-gradient(180deg,#7a4c7a,var(--mauve-deep))}
.app-title{left:348px;top:597px;font-size:10px;font-weight:500;color:#fff}
.app-text{left:348px;top:616px;width:194px;font-size:5.3px;line-height:11px;color:#fff}
.app-btn{left:349px;top:679px;width:86px;height:22px;background:#d9d9d9;border-radius:2px;display:flex;align-items:center;font-family:"Delius",cursive;font-size:7px;color:#555}
.app-btn i{width:22px;height:22px;background:#c6c6c6;display:flex;align-items:center;justify-content:center;margin-right:8px}

/* articles */
.heading-left{font-size:11px;font-weight:400;color:var(--plum)}
.heading-left em{font-style:normal;color:var(--gold)}
.article{top:779px;width:149px}
.article .thumb{height:70px}
.article h4{font-size:7px;font-weight:400;color:var(--plum);margin-top:9px}
.article p{font-size:5px;line-height:11px;color:#444;margin-top:3px}
.article .more{color:#222;margin-top:1px}

/* blog */
.blog-rule{left:309px;top:962px;width:90px;height:1px;background:#999}
.blog-rule::after{content:"";position:absolute;left:42px;top:-2px;width:5px;height:5px;border-radius:50%;background:#888}
.post{top:977px;display:flex;gap:9px}
.post .photo{flex:none;position:relative;width:116px;height:78px;border:3px solid #eee;box-shadow:0 0 2px rgba(0,0,0,.35)}
.post .tag{position:absolute;left:2px;top:3px;height:12px;padding:0 6px;background:var(--plum);color:#fff;font-size:5px;display:flex;align-items:center;gap:6px}
.post .body{width:102px}
.post h5{font-size:6.5px;font-weight:500;color:var(--gold)}
.post .meta{font-size:4.8px;color:#666;margin-top:5px}
.post p{font-size:5px;line-height:8.2px;color:#555;margin-top:6px}
.post .more{color:#234;margin-top:5px}

/* clients */
.clients{left:127px;top:1077px;width:430px;display:flex;justify-content:space-between;font-size:8.5px;font-weight:500;color:#666}

/* newsletter */
.newsletter{left:0;top:1102px;width:690px;height:55px;background:var(--leaf)}
.newsletter-fold{left:355px;top:1102px;width:0;height:0;border-top:55px solid var(--leaf-dark);border-right:55px solid transparent}
.news-title{left:113px;top:1109px;font-size:11px;font-weight:700;color:#fff;letter-spacing:.6px}
.news-text{left:113px;top:1126px;width:224px;font-size:5.3px;line-height:7px;color:#fff}
.news-input{left:411px;top:1122px;width:109px;height:18px;background:#f2f2f2}
.news-btn{left:520px;top:1122px;width:53px;height:18px;background:var(--lavender);color:#fff;font-size:5.5px;font-weight:500;display:flex;align-items:center;justify-content:center}

/* footer */
.footer{left:0;top:1157px;width:690px;height:43px;background:var(--night)}
.foot-links{left:114px;top:1170px;font-size:5px;color:#fff}
.foot-copy{left:114px;top:1183px;font-size:5px;color:#fff}
.social{left:514px;top:1170px;display:flex;gap:4px}
.social span{width:18px;height:18px;border-radius:50%;background:#e6e6e6;color:#111;font-size:4.5px;display:flex;align-items:center;justify-content:center}
</style>
</head>
<body>

<div class="abs topline"></div>
<header>
  <div class="abs brand"><span class="brand-mark"></span><span class="brand-name">plumbwick</span></div>
  <nav class="abs nav">
    <a class="active">Home</a><a>About us</a><a>What we do</a><a>News</a><a>blog</a><a>Articles</a><a>Clients</a><a>Partners</a>
  </nav>
</header>

<section>
  <div class="abs hero" role="img" aria-label="Hero photo: a dusky city skyline with a technology light bulb illustration"></div>
  <h1 class="abs hero-title">Serious It support For Business</h1>
  <div class="abs hero-arrow" style="left:0"><svg width="6" height="9" viewBox="0 0 6 9"><path d="M5 1 1.5 4.5 5 8" stroke="#fff" stroke-width="1.6" fill="none"/></svg></div>
  <div class="abs hero-arrow" style="left:672px"><svg width="6" height="9" viewBox="0 0 6 9"><path d="M1 1 4.5 4.5 1 8" stroke="#fff" stroke-width="1.6" fill="none"/></svg></div>
  <div class="abs hero-dots"><span class="on"></span><span></span><span></span></div>
</section>

<section>
  <div class="abs welcome"></div>
  <h2 class="abs section-title" style="top:329px">Welcome To <em>Plumbwick</em></h2>
  <p class="abs welcome-text">Lorem ipsum dolor sit amet, consectetur adipiscing elit. Consectetur adipiscing elit, sed do eiusmod tempor incididunt ut labore et dolore magna aliqua. Ut enim ad minim veniam, quis nostrud.Lorem ipsum dolor sit amet, consectetur adipiscing elit. Consectetur adipiscing elit, sed do eiusmod tempor incididunt ut labore et dolore magna aliqua. Ut enim ad minim veniam, quis nostrud.Lorem ipsum dolor sit amet, consectetur adipiscing elit. Consectetur adipiscing elit, sed do eiusmod tempor incididunt ut labore et dolore magna aliqua. Ut enim ad minim veniam, quis nostrud.</p>
</section>

<section>
  <h2 class="abs section-title" style="top:430px">Services</h2>
  <div class="abs services">
    <div class="service">
      <svg viewBox="0 0 30 24" width="28"><circle cx="10" cy="9" r="5" fill="none" stroke="#d9a400" stroke-width="2.4" stroke-dasharray="2.5 1.5"/><circle cx="10" cy="9" r="1.8" fill="#d9a400"/><rect x="12" y="12" width="14" height="9" fill="none" stroke="#d9a400" stroke-width="1.6"/><path d="M9 22h20" stroke="#d9a400" stroke-width="1.6"/></svg>
      <h3>IT Support &amp; Mangement</h3>
      <p>Lorem ipsum dolor sit amet, consectetur adipiscing elit. Consectetur adipiscing elit, sed do eiusmod</p>
      <span class="more">Read More +</span>
    </div>
    <div class="service">
      <svg viewBox="0 0 30 24" width="28"><path d="M8 20a6 6 0 0 1 0-12 8 8 0 0 1 15 2 5 5 0 0 1 0 10z" fill="#d9a400"/><circle cx="15" cy="14" r="3.5" fill="none" stroke="#fff" stroke-width="1.3"/></svg>
      <h3>Cloud Computing</h3>
      <p>Lorem ipsum dolor sit amet, consectetur adipiscing elit. Consectetur adipiscing elit, sed do eiusmod</p>
      <span class="more">Read More +</span>
    </div>
    <div class="service">
      <svg viewBox="0 0 30 24" width="28"><ellipse cx="12" cy="5" rx="8" ry="3" fill="#d9a400"/><path d="M4 7v4c0 2 16 2 16 0V7c0 2-16 2-16 0zm0 6v4c0 2 16 2 16 0v-4c0 2-16 2-16 0z" fill="#d9a400"/><path d="M22 13v8M18 17h8" stroke="#d9a400" stroke-width="2.4"/></svg>
      <h3>Disaster Recovery</h3>
      <p>Lorem ipsum dolor sit amet, consectetur adipiscing elit. Consectetur adipiscing elit, sed do eiusmod</p>
      <span class="more">Read More +</span>
    </div>
    <div class="service">
      <svg viewBox="0 0 30 24" width="28"><rect x="11" y="1" width="8" height="6" fill="#d9a400"/><path d="M15 7v5M5 12h20M5 12v4M15 12v4M25 12v4" stroke="#d9a400" stroke-width="1.5" fill="none"/><rect x="1" y="16" width="8" height="6" fill="#d9a400"/><rect x="11" y="16" width="8" height="6" fill="#d9a400"/><rect x="21" y="16" width="8" height="6" fill="#d9a400"/></svg>
      <h3>Virtalosation</h3>
      <p>Lorem ipsum dolor sit amet, consectetur adipiscing elit. Consectetur adipiscing elit, sed do eiusmod</p>
      <span class="more">Read More +</span>
    </div>
    <div class="service">
      <svg viewBox="0 0 30 24" width="28"><path d="M15 1 25 6v12l-10 5L5 18V6z" fill="none" stroke="#d9a400" stroke-width="1.8"/><path d="M5 6l10 5 10-5M15 11v12" stroke="#d9a400" stroke-width="1.8" fill="none"/><path d="M15 11 25 6v12l-10 5z" fill="#d9a400"/></svg>
      <h3>CAD Services</h3>
      <p>Lorem ipsum dolor sit amet, consectetur adipiscing elit. Consectetur adipiscing elit, sed do eiusmod</p>
      <span class="more">Read More +</span>
    </div>
  </div>
</section>

<section>
  <div class="abs app"></div>
  <div class="abs app-visual" role="img" aria-label="App preview illustration: a smartphone with labelled feature callouts"></div>
  <h2 class="abs app-title">What We Do</h2>
  <p class="abs app-text">Lorem ipsum dolor sit amet, consectetur adipiscing elit. Nulla convallis egestas rhoncus. Donec facilisis fermentum sem, ac viverra ante luctus vel. Donec vel mauris quam. Aliquam pellentesque pellentesque turpis, ut bibendum sapien sollicitudin nec. Pellentesque posuere ornare placerat. Suspendisse potenti. Quisque massa torto.</p>
  <div class="abs app-btn"><i><svg width="7" height="11" viewBox="0 0 7 11"><rect x=".6" y=".6" width="5.8" height="9.8" rx="1" fill="none" stroke="#555" stroke-width="1"/></svg></i>Get this App</div>
</section>

<section>
  <h2 class="abs heading-left" style="left:114px;top:757px">Latest <em>Articles</em></h2>
  <article class="abs article" style="left:115px">
    <div class="thumb" role="img" aria-label="Article photo: a person surrounded by floating screens" style="background:linear-gradient(180deg,#cfe6f2,#7fb4cf)"></div>
    <h4>Shrove Tuesday 65 calorie Pancakes</h4>
    <p>No need to miss out on Pancake day! Pancakes are really easy to make and it is something that the whole family can get involved with from making the batter to adding the fillings, and kids love them, especially the flipping!</p>
    <span class="more">Read More +</span>
  </article>
  <article class="abs article" style="left:270px">
    <div class="thumb" role="img" aria-label="Article photo: a figure on a rising arrow against the sky" style="background:linear-gradient(180deg,#7fa9c9,#d9e7f0)"></div>
    <h4>Salmon &amp; Asparagus Salad with Raspberries</h4>
    <p>No need to miss out on Pancake day! Pancakes are really easy to make and it is something that the whole family can get involved with from making the batter to adding the fillings, and kids love them, especially the flipping!</p>
    <span class="more">Read More +</span>
  </article>
  <article class="abs article" style="left:425px">
    <div class="thumb" role="img" aria-label="Article photo: a hand releasing glowing app icons" style="background:linear-gradient(180deg,#1c1c1c,#3a4a3a)"></div>
    <h4>Salmon &amp; Asparagus Salad</h4>
    <p>No need to miss out on Pancake day! Pancakes are really easy to make and it is something that the whole family can get involved with from making the batter to adding the fillings, and kids love them, especially the flipping!</p>
    <span class="more">Read More +</span>
  </article>
</section>

<section>
  <h2 class="abs section-title" style="top:943px;font-size:11px">From The <em>Blog</em></h2>
  <div class="abs blog-rule"></div>
  <article class="abs post" style="left:115px">
    <div class="photo" role="img" aria-label="Blog photo: a team meeting in a bright office" style="background:linear-gradient(180deg,#e9eef2,#b9c4cc)"><span class="tag">April 06 2013 <span>12</span></span></div>
    <div class="body">
      <h5>Nullamdignisim vivera sceler</h5>
      <div class="meta">teger, luctus, mor, purus</div>
      <p>Lorem ipsum dolor sit amet, consectet adipiscing elit. Praesent pulvinar massa nec augue malesuada in Lorem ipsum dolor sit amet</p>
      <span class="more">Read More +</span>
    </div>
  </article>
  <article class="abs post" style="left:345px">
    <div class="photo" role="img" aria-label="Blog photo: a business team standing together" style="background:linear-gradient(180deg,#6f6a66,#2f2f33)"><span class="tag">April 06 2013 <span>12</span></span></div>
    <div class="body">
      <h5>Nullamdignisim vivera sceler</h5>
      <div class="meta">teger, luctus, mor, purus</div>
      <p>Lorem ipsum dolor sit amet, consectet adipiscing elit. Praesent pulvinar massa nec augue malesuada in Lorem ipsum dolor sit amet</p>
      <span class="more">Read More +</span>
    </div>
  </article>
</section>

<section class="abs clients">
  <span>Fernvale</span><span>Quillo</span><span>Netwright</span><span>Briar</span><span>Orvanta</span><span>Telva</span><span>Hollin</span><span>Crestel</span><span>Ondra</span>
</section>

<section>
  <div class="abs newsletter"></div>
  <div class="abs newsletter-fold"></div>
  <h2 class="abs news-title">SIGN UP TO OUT NEWSLETTER :</h2>
  <p class="abs news-text">Duis autem vel eum iriure dolor in hendrerit in vulputate velit esse mole stie consequat, vel illum dolore eu feugiat nulla facilisis at vero eros et accumsan et iusto odio dignissim qui blandit praesent luptatum.</p>
  <div class="abs news-input"></div>
  <div class="abs news-btn">SUBSCRIBE</div>
</section>

<footer>
  <div class="abs footer"></div>
  <div class="abs foot-links">Home About Us Services Portfolio Blog Contact Us</div>
  <div class="abs foot-copy">© copyright 2014 Plumbwick all rights reserved.</div>
  <div class="abs social"><span>Nook</span><span>Pip</span><span>Hub</span></div>
</footer>

</body>
</html>
```